We are a building company that build new homes and units we are looking for something fresh and looks good my company name is
Lark Building Co Pty Ltd

Industry/Entity Type

Building

Contact Information for Business Card

Name Marco Ellis-Dunford
Tittle: Director
Address 14 Corrin St. Pelham Vale Vic 3179
Ph: 03 9582 4063
Mobile : 0400 362 918

www.larkbuildingco.com.au
Email: sales@larkbuildingco.com.au

```html
<!DOCTYPE html>
<html lang="en">
<head>
<meta charset="utf-8">
<title>Lark Building Co Pty Ltd – Business Card</title>
<link rel="stylesheet" href="https://fonts.googleapis.com/css2?family=Exo+2:wght@400;500;600;700&display=swap">
<style>
  :root {
    --page: #f1f1ee;
    --card: #000000;
    --red: #ec1c24;
    --white: #ffffff;
    --rule: #5a5a5a;
  }
  * { margin: 0; padding: 0; box-sizing: border-box; }
  html, body { width: 1189px; height: 1200px; overflow: hidden; }
  body {
    background: var(--page);
    font-family: "Exo 2", sans-serif;
    color: var(--white);
    position: relative;
  }
  .card {
    position: absolute;
    left: 172px;
    width: 855px;
    height: 487px;
    background: var(--card);
    border-radius: 16px;
    overflow: hidden;
  }
  .card--front { top: 68px; }
  .card--back { top: 627px; }

  .wordmark {
    position: absolute;
    color: var(--red);
    font-weight: 700;
    text-align: center;
    line-height: 1.1;
    text-transform: uppercase;
  }
  .card--front .wordmark {
    left: 0; right: 0;
    top: 150px;
    font-size: 56px;
    letter-spacing: 1px;
  }
  .card--back .wordmark {
    left: 40px; width: 304px;
    top: 205px;
    font-size: 34px;
  }

  .front-web {
    position: absolute;
    left: 0; right: 0;
    top: 390px;
    text-align: center;
    font-size: 29px;
    font-weight: 500;
  }

  .acn {
    position: absolute;
    left: 40px; width: 304px;
    top: 310px;
    text-align: center;
    color: var(--red);
    font-size: 22px;
    font-weight: 600;
  }

  .divider {
    position: absolute;
    left: 377px; top: 106px;
    width: 1px; height: 263px;
    background: var(--rule);
  }

  .person {
    position: absolute;
    left: 409px; top: 102px;
  }
  .person__name {
    color: var(--red);
    font-size: 36px;
    font-weight: 700;
    line-height: 1.1;
  }
  .person__title {
    font-size: 25px;
    font-weight: 500;
    line-height: 1.1;
  }

  .contacts {
    position: absolute;
    left: 409px; top: 231px;
    list-style: none;
  }
  .contacts li {
    display: flex;
    align-items: center;
    height: 33.5px;
    font-size: 24px;
    font-weight: 500;
  }
  .contacts svg {
    width: 24px; height: 24px;
    margin-right: 11px;
    flex: none;
  }

  .address-band {
    position: absolute;
    left: 0; right: 0; bottom: 0;
    height: 53px;
    background: var(--red);
    display: flex;
    align-items: center;
    justify-content: center;
    font-size: 24px;
    font-weight: 500;
  }
</style>
</head>
<body>

<section class="card card--front">
  <div class="wordmark">Lark Building Co<br>Pty Ltd</div>
  <p class="front-web">www.larkbuildingco.com.au</p>
</section>

<section class="card card--back">
  <div class="wordmark">Lark Building Co<br>Pty Ltd</div>
  <p class="acn">A.C.N: 41 587 902 316</p>

  <div class="divider"></div>

  <div class="person">
    <h1 class="person__name">Marco Ellis-Dunford</h1>
    <p class="person__title">Managing Director</p>
  </div>

  <ul class="contacts">
    <li>
      <svg viewBox="0 0 24 24" aria-hidden="true">
        <rect width="24" height="24" rx="4" fill="var(--red)"/>
        <rect x="8.5" y="4" width="7" height="16" rx="1.2" fill="none" stroke="#fff" stroke-width="1.6"/>
        <rect x="10" y="6.5" width="4" height="5" fill="#fff"/>
      </svg>
      0400 362 918
    </li>
    <li>
      <svg viewBox="0 0 24 24" aria-hidden="true">
        <rect width="24" height="24" rx="4" fill="var(--red)"/>
        <path d="M4.5 10c0-3 15-3 15 0v1.5h-3.5v-1.8h-8v1.8H4.5z" fill="#fff"/>
        <path d="M7 13l2-2.5h6l2 2.5v4.5H7z" fill="#fff"/>
        <circle cx="12" cy="14.5" r="1.6" fill="var(--red)"/>
      </svg>
      03 9582 4063
    </li>
    <li>
      <svg viewBox="0 0 24 24" aria-hidden="true">
        <rect width="24" height="24" rx="4" fill="var(--red)"/>
        <rect x="4.5" y="6.5" width="15" height="11" fill="#fff"/>
        <path d="M4.5 6.5l7.5 6.5 7.5-6.5M4.5 17.5l5.5-5.5M19.5 17.5l-5.5-5.5" fill="none" stroke="var(--red)" stroke-width="1.3"/>
      </svg>
      sales@larkbuildingco.com.au
    </li>
    <li>
      <svg viewBox="0 0 24 24" aria-hidden="true">
        <rect width="24" height="24" rx="12" fill="var(--red)"/>
        <g fill="none" stroke="#fff" stroke-width="1.3">
          <circle cx="12" cy="12" r="6.5"/>
          <ellipse cx="12" cy="12" rx="3" ry="6.5"/>
          <path d="M5.5 12h13M6.5 8.8h11M6.5 15.2h11"/>
        </g>
      </svg>
      www.larkbuildingco.com.au
    </li>
  </ul>

  <div class="address-band">14 Corrin St Pelham Vale Vic 3179</div>
</section>

</body>
</html>
```